Poloshirt Packaging

We need a very attractive packaging design for our poloshirts. We are wholesaler of the schoolwear market. See what we currently have. I dont want any specific sizing put on the packaging. One design for all poloshirts (2 sides).
our logo is attached aswell

Target Market(s)

Parents

Requirements
Must have
• Our logo
Should not have
• size or age

```html
<!DOCTYPE html>
<html lang="en">
<head>
<meta charset="UTF-8">
<title>Novastride Poloshirt Packaging</title>
<link rel="stylesheet" href="https://fonts.googleapis.com/css2?family=Montserrat:wght@600;700&family=Oswald:wght@700&family=Roboto+Condensed:wght@400&display=swap">
<style>
  :root {
    --navy: #143a64;
    --red: #e3222f;
    --white: #ffffff;
    --frame: #222222;
  }
  html, body {
    margin: 0;
    padding: 0;
    overflow: hidden;
    background: var(--white);
  }
  .pack-face {
    position: relative;
    width: 849px;
    height: 1200px;
    box-sizing: border-box;
    border: 1px solid var(--frame);
    background: var(--white);
    overflow: hidden;
  }
  .brand-name {
    position: absolute;
    left: 0;
    right: 0;
    top: 676px;
    margin: 0;
    text-align: center;
    font-family: "Montserrat", sans-serif;
    font-weight: 600;
    font-size: 112px;
    letter-spacing: -2px;
    line-height: 1;
    color: var(--navy);
  }
  .feature-bar {
    position: absolute;
    left: 158px;
    top: 865px;
    width: 531px;
    height: 27px;
    background: var(--navy);
    color: var(--white);
    font-family: "Montserrat", sans-serif;
    font-weight: 700;
    font-size: 16px;
    line-height: 27px;
    text-align: center;
    white-space: nowrap;
  }
  .feature-bar .divider {
    font-weight: 400;
    margin: 0 5px;
  }
  .product-panel {
    position: absolute;
    left: 158px;
    top: 898px;
    width: 533px;
    height: 163px;
    background: var(--red);
    display: flex;
    align-items: center;
    justify-content: center;
  }
  .product-name {
    margin: 0;
    font-family: "Oswald", sans-serif;
    font-weight: 700;
    font-size: 112px;
    line-height: 1;
    color: var(--white);
    letter-spacing: 1px;
  }
  .thanks-note {
    position: absolute;
    left: 0;
    right: 0;
    top: 1084px;
    margin: 0;
    text-align: center;
    font-family: "Roboto Condensed", sans-serif;
    font-weight: 400;
    font-size: 23px;
    line-height: 40px;
    color: var(--red);
  }
</style>
</head>
<body>
  <main class="pack-face">
    <h1 class="brand-name">Novastride</h1>
    <div class="feature-bar">
      Superior weight fabric<span class="divider">|</span>Easy Care - Low iron<span class="divider">|</span>Reactive Dyes
    </div>
    <div class="product-panel">
      <h2 class="product-name">POLOSHIRT</h2>
    </div>
    <p class="thanks-note">
      Thanks You for Buying Our Product and Ask your<br>
      Local Supplier abt the Rest Of Novastride Range
    </p>
  </main>
</body>
</html>
```